BOLD & MINIMALIST DESIGN NEEDED

We want a very bold but minimalistic business card design that is impactful and utilizes both sides of the business card. Our current logo is included for your use.

We want bold fonts and good use of negative space. We don't want the logo to overpower the design.

Target Market(s)

Professionals who are building new commercial buildings.

Industry/Entity Type

Construction

Contact Information for Business Card

Name, Title, email, office phone, cell phone, website

Font styles to use
Serif
Sans Serif

Requirements
Must have
• Bold design!

```html
<!DOCTYPE html>
<html lang="en">
<head>
<meta charset="utf-8">
<title>Ridgeline Design + Build — Business Card</title>
<link href="https://fonts.googleapis.com/css2?family=Montserrat:wght@400;500;700;800&display=swap" rel="stylesheet">
<style>
  :root {
    --backdrop: #2a2a2a;
    --card-black: #141414;
    --card-white: #ffffff;
    --brand-green: #7dc242;
    --ink: #1a1a1a;
    --ink-soft: #333333;
  }
  * { box-sizing: border-box; margin: 0; padding: 0; }
  html, body {
    width: 1200px; height: 874px; overflow: hidden;
    background: var(--backdrop);
    font-family: "Montserrat", sans-serif;
  }
  .stage {
    width: 1200px; height: 874px;
    display: flex; flex-direction: column;
    align-items: center; justify-content: center; gap: 40px;
  }
  .card {
    position: relative;
    width: 640px; height: 366px;
    border-radius: 22px;
    overflow: hidden;
    box-shadow: 0 10px 30px rgba(0,0,0,.45);
  }
  /* Front side */
  .card--front {
    background: var(--card-black);
    display: flex; align-items: center; justify-content: center;
  }
  .brand {
    display: flex; align-items: center; gap: 14px;
  }
  .brand__mark {
    width: 22px; height: 22px;
    background: var(--brand-green);
  }
  .brand__name {
    font-weight: 800;
    color: #ffffff;
    font-size: 44px;
    letter-spacing: 1px;
    line-height: 1;
    text-transform: uppercase;
  }
  .brand__name--small { font-size: 30px; color: var(--ink); }
  .brand__tag {
    font-weight: 800;
    text-transform: uppercase;
    letter-spacing: 1px;
  }
  /* Back side */
  .card--back { background: var(--card-white); }
  .back__swoosh {
    position: absolute; left: 0; bottom: 0;
    width: 640px; height: 200px;
  }
  .back__brand {
    position: absolute; left: 42px; top: 118px;
    display: flex; flex-direction: column; gap: 8px;
  }
  .back__brand .brand__sub {
    font-weight: 800; font-size: 30px; color: var(--ink);
    text-transform: uppercase; line-height: 1;
  }
  .back__divider {
    position: absolute; left: 318px; top: 40px;
    width: 2px; height: 230px;
    background: var(--brand-green);
  }
  .contact {
    position: absolute; left: 340px; top: 40px;
    color: var(--ink-soft);
  }
  .contact__name {
    font-weight: 700; font-size: 27px; color: var(--brand-green);
    text-transform: uppercase; letter-spacing: .5px;
  }
  .contact__title {
    font-weight: 500; font-size: 14px; letter-spacing: .5px;
    margin-top: 2px; text-transform: uppercase;
  }
  .contact__address {
    font-size: 15px; line-height: 1.4; margin-top: 18px;
  }
  .contact__list { list-style: none; margin-top: 14px; }
  .contact__item {
    display: flex; align-items: center; gap: 8px;
    font-size: 15px; line-height: 1.55;
  }
  .contact__icon { width: 13px; height: 13px; flex: none; }
</style>
</head>
<body>
<main class="stage">
  <section class="card card--front" aria-label="Card front">
    <div class="brand">
      <span class="brand__mark"></span>
      <span class="brand__name">Ridgeline Design + Build</span>
    </div>
  </section>

  <section class="card card--back" aria-label="Card back">
    <svg class="back__swoosh" viewBox="0 0 640 200" preserveAspectRatio="none" aria-hidden="true">
      <path d="M0 20 C 60 110, 200 140, 330 120 C 450 100, 560 120, 640 170 L640 200 L0 200 Z" fill="#7dc242"/>
      <path d="M0 10 C 60 100, 200 128, 330 110 C 450 92, 560 112, 640 160 L640 170 C 560 120, 450 100, 330 120 C 200 140, 60 110, 0 20 Z" fill="#141414"/>
    </svg>

    <div class="back__brand">
      <div class="brand">
        <span class="brand__mark"></span>
        <span class="brand__name brand__name--small">Ridgeline</span>
      </div>
      <span class="brand__sub">Design + Build</span>
    </div>

    <div class="back__divider"></div>

    <div class="contact">
      <h1 class="contact__name">Marcus Vale</h1>
      <p class="contact__title">Owner-CEO</p>
      <p class="contact__address">Your address, City<br>State, Zip 1234</p>
      <ul class="contact__list">
        <li class="contact__item">
          <svg class="contact__icon" viewBox="0 0 16 16"><path fill="#7dc242" d="M3 1h3l1.5 4-2 1.2a9 9 0 0 0 4.3 4.3L11 8.5l4 1.5v3a2 2 0 0 1-2 2A12 12 0 0 1 1 3a2 2 0 0 1 2-2z"/></svg>
          123 456 789
        </li>
        <li class="contact__item">
          <svg class="contact__icon" viewBox="0 0 16 16"><rect x="4" y="1" width="8" height="14" rx="1.5" fill="none" stroke="#7dc242" stroke-width="1.6"/><circle cx="8" cy="12.5" r="1" fill="#7dc242"/></svg>
          123 456 789
        </li>
        <li class="contact__item">
          <svg class="contact__icon" viewBox="0 0 16 16"><rect x="1" y="3" width="14" height="10" fill="#7dc242"/><path d="M1 3l7 6 7-6" fill="none" stroke="#fff" stroke-width="1.3"/></svg>
          info@yourmail.com
        </li>
        <li class="contact__item">
          <svg class="contact__icon" viewBox="0 0 16 16"><circle cx="8" cy="8" r="7" fill="#7dc242"/><path d="M1 8h14M8 1c3 3 3 11 0 14M8 1c-3 3-3 11 0 14" fill="none" stroke="#fff" stroke-width="1"/></svg>
          www.yourwebsite.com
        </li>
      </ul>
    </div>
  </section>
</main>
</body>
</html>
```